Digital Imaging Website Design Project

This project is for 3 page designs - The main Home page design, department page design & content page design which will utilize most of the home page components.

Client Background - http://www.klmvxco.example

An almost Forty year old established printing company that has a large client base of architect/engineering, as the print shop opened up as a blueprinting company, and over the years has grown, changed and expanded to offer document and digital file management for this industry. KLMVxco. has also always offered color printing services, but recently has expanded their color department to be able to offer amazing dimensional printing, and extreme cutting technology.

These new products and services will be targeted to new industries for repeatable printing needs, promotional, point of purchase color printing, as well as in-store, interior decor/wall. These new printing services are only offered by KLMVXCO in their area, and they want to convey that they are on the leading edge of color printing technology, while at the same time, not eliminating their existing primary business scaring away their traditional client base of architectural/engineering firms that use them for large format printing, scanning and document management services.

1 - Home Page Design
Primary Goals of the design:

1.Provide a new, eye catching engaging website that conveys the above expansion/growth/cutting edge company.
2.Full screen design please to move away from the 'center' bordered up website they currently have.
3.Design Components – We don't have any media to provide you with exception of our logo. We're looking for fresh design that is exciting and engaging imagery. Additionally, we are working on a color/effected version of our logo to place on the color division page, and this will probably tie in with the design you create for us.
4.It should be designed to be able to work as a responsive design as well so that when installed, will work across devices etc..
5.Colors – Same color scheme, but if you have an accent color you'd like to use to make the site pop, go for it!

Requirements:
1.The 4 divisions of the company should be the main feature so that the client depending on which department they are needing, will see those 4 choices clearly in the design, and they'll know to click on one of them to get more information and to their needed services.

2.The main goal of the site is to get visitors to place an order, there should be a feature on the home page for this call to action.

3.Put in an element that communicates the main benefit of KLMVxco. - an area for a 1-line Statement/Call to Action / Overall Company Benefit/

4.The 4 divisions need to have eye catching elements related to their products and services, and that clearly illustrate that the user should click on that to go to the appropriate area for products and services

Reprographics
This department is specifically geared to architect/engineering industry
BYLine for optional Use: Partnering with Building Industry Providers since 1975
Related pages for better understanding:
http://www.klmvxco.example/services/portland_professional_printing_services
http://www.klmvxco.example/services/reprographics
Digital File Management
This department is related to Architect/engineers, but can also apply to any other industry needing electronic document management, scanning, or archival services.
BYLine for optional use: Effective & Efficient Digital Solutions at every level.
Related Pages:
http://www.klmvxco.example/colorgraphics/electronic_file_document_management
http://www.klmvxco.example/colorgraphics/document_scanning_service
http://www.klmvxco.example/services/scanning_and_archiving

Color Graphics
This Department is newly expanded / has expanded services / they are focusing more of their efforts on this department and is a key reason for updated website design.
This Department image/representation should be stellar in the imagery to convey the excellence of the color department the services availble.
One of their newest products/services is dimensional printing – not 3-D, but raised element printing. Essentially a client could pick components on their graphic that that they want to 'bump' out, and additional layers would be put in place to create a popped out, dimensional effect. * Bonus points for creating the color department image that effectively conveys this new service – whether it's showing an abstract image/element that is actually raised off the page/paper/component. Additionally the color dimensional printing can be done on practically any material – glass, vinyl, material etc.... Please let me know if you have any questions on this.
BYLine for optional Use: See How Our Color Stands Out From the Rest
Related pages:
http://www.klmvxco.example/colorgraphics
http://www.klmvxco.example/colorgraphics/color_digital_imaging

Equipment & Supplies
This department provides specific supplies and hardware vs. printing products/services. Our largest client base is architects/engineers, but is not limited to this industry. Typical equipment is large printers, and supplies are typically paper products geared to the large format printing services, for the architect/engineers industry.
Byline for optional Use: In-House Printing & Fulfillment Services
Related pages:
http://www.klmvxco.example/tarvo_ulix_equipment_sales
http://www.klmvxco.example/supplies

Additionally - Possibly have descriptive text sections below these 4 elements, but this is optional.

2.) Department/Division Page design -

This page should pull the home page element to over based on which division is selected.
Have a submenu design incorporated so that users can navigate to all the products and services that will be listed under that division
Contain a plugin design for FAQs – so that depending on which division page they are on, the appropriate FAQ's would display for use to have easy access to.
Contain a plugin design for – Contact Us easy form – short form –
Name
Company
Number
Email
Project Details/Questions: Text box

3.)Content Page design
This page should have main area for content
Area for an image with slideshow of other supporting images
Optional area for video – most (99%) of the pages will not have videos, but in the case we do, would like an area that will display videos effectively.
Optional FAQ plugin display
Contact plugin display

Global Elements:

Static and very visible site features that are in a position so that if user clicks beyond home page will still see these are:
Get a Quote
Place Order
Digital Plan-room
Call Today - 555-384-7290

Other global components:
SM Icons – QN, Chirpa, Workrung
Rotating Testimonial

Navigational Menu:
The KLMVXCO Difference
About
Sustainability
Products & Services
Reprograhics
Digital File Management
Color Graphics
Equipment & Supplies
Login
Blog
Contact Us

After the contest – What would be great to have is when a user clicks on one of the departments, it takes that visual element and continues onto it's department page for a smaller but related image - But this may be an after this web design contest.

Additionally will need some other design work on the interior pages, as well, so hoping to find a great designer to complete the other tasks – as well as be the go-to for future endeavors!

Thanks for looking at the project, and I look forward to any questions you may have.
Updates

Looking forward to hearing from interested designers! - If you're curious about my work, you can find my profile at:  https://www.jobrilly.example/users/~07f3b92e61cd5a0b48

Target Market(s)

Please see description

Industry/Entity Type

Electronic

Requirements
Must have
• Please see description

```html
<!DOCTYPE html>
<html lang="fr">
<head>
<meta charset="utf-8">
<title>KLMVxco. – Services for Architects, Engineers &amp; Builders</title>
<link href="https://fonts.googleapis.com/css2?family=Open+Sans:wght@300;400;600;700&display=swap" rel="stylesheet">
<style>
:root{
  --red:#e0393e;
  --red-dark:#c4262b;
  --navy:#2e3192;
  --heading:#2b3a8c;
  --text:#777;
  --box1:#3db4e7;
  --box2:#0a86d0;
  --box3:#2e5ba9;
  --box4:#2b2f87;
  --footer:#2a2a2a;
  --footer-text:#a5a5a5;
  --line:#dcdcdc;
}
*{box-sizing:border-box;margin:0;padding:0}
html,body{width:951px;height:1200px;overflow:hidden;background:#fff}
body{font-family:'Open Sans',sans-serif;color:var(--text);position:relative}
a{color:inherit;text-decoration:none}
.abs{position:absolute}

/* utility bar */
.utility{left:0;top:0;width:951px;height:19px;background:#f4f4f4;border-bottom:1px solid #e8e8e8}
.utility ul{position:absolute;right:79px;top:3px;display:flex;gap:16px;list-style:none;font-size:9px;color:#555}
.utility li{display:flex;align-items:center;gap:3px}

/* header */
.brand{left:79px;top:40px;display:flex;align-items:center;gap:8px;font-weight:700;font-size:30px;color:var(--navy);letter-spacing:-.5px}
.brand .mark{width:16px;height:16px;background:var(--navy)}
.call{left:583px;top:49px;font-size:13px;color:#555}
.call strong{color:var(--red);font-weight:700}
.place-order{left:719px;top:40px;width:153px;height:34px;border-radius:17px;background:linear-gradient(#e8474b,var(--red-dark));color:#fff;font-weight:700;font-size:15px;display:flex;align-items:center;justify-content:center;gap:7px;box-shadow:0 1px 2px rgba(0,0,0,.3)}

/* navigation */
.nav-rule{left:0;top:127px;width:951px;height:1px;background:var(--line)}
.main-nav{left:79px;top:94px;width:793px;height:34px;display:flex;background:linear-gradient(#fafafa,#e9e9e9);border:1px solid #d4d4d4;border-bottom:none;list-style:none}
.main-nav li{display:flex;align-items:center;justify-content:center;font-size:9.2px;color:#555;border-right:1px solid #d0d0d0;white-space:nowrap}
.main-nav li:last-child{border-right:none}
.main-nav li.active{background:var(--navy);color:#fff}

/* hero */
.hero-art{left:260px;top:128px;width:691px;height:416px;background:linear-gradient(100deg,#fff 0%,#fff 8%,#f3e8b0 22%,#f2b234 32%,#e2432c 42%,#a3247c 52%,#3a6fc0 60%,#4aa96a 68%,#e9e6df 78%,#f2f2f0 100%)}
.hero-title{left:79px;top:166px;font-size:26px;font-weight:300;color:var(--red);line-height:31px}
.hero-copy{left:80px;top:236px;width:300px;font-size:11.5px;line-height:17.5px;color:#666}
.btn-red{border-radius:14px;background:linear-gradient(#e6474b,var(--red-dark));color:#fff;font-weight:700;display:flex;align-items:center;justify-content:center;box-shadow:0 1px 2px rgba(0,0,0,.35)}
.read-more-hero{left:80px;top:320px;width:97px;height:26px;font-size:13px}

/* divisions */
.divisions{left:79px;top:389px;width:793px;height:155px;display:flex;border-bottom:2px solid var(--navy)}
.division{flex:1;padding:13px 12px 0;color:#fff}
.division:nth-child(1){background:var(--box1)}
.division:nth-child(2){background:var(--box2)}
.division:nth-child(3){background:var(--box3)}
.division:nth-child(4){background:var(--box4)}
.division h2{display:flex;gap:6px;font-weight:300;font-size:17.5px;line-height:18px;height:38px}
.division h2 svg{flex:none;margin-top:8px}
.division p{font-size:9.3px;line-height:12.8px;margin-top:10px;height:52px}
.division .more{display:inline-flex;align-items:center;gap:6px;border:1px solid #fff;font-size:9.6px;padding:3px 8px;margin-top:9px}
.section-rule{left:0;top:543px;width:951px;height:1px;background:var(--line)}

/* content */
h3.title{font-weight:400;color:var(--heading);font-size:19px}
h4.title{font-weight:400;color:var(--heading);font-size:16px}
.welcome{left:79px;top:568px;width:500px}
.welcome p{font-size:9.5px;line-height:16px;margin-top:8px}
.welcome h3{margin-bottom:4px}
.news{left:79px;top:728px;width:500px}
.news-item{display:flex;gap:13px;margin-top:12px;height:58px}
.news-item + .news-item{margin-top:12px}
.news-item .thumb{width:63px;height:55px;flex:none;background:linear-gradient(135deg,#dfe8f3,#8fb0d6)}
.news-item:nth-child(3) .thumb{background:linear-gradient(135deg,#1d4d86,#3a78b6)}
.news-item time{font-size:9.6px;color:var(--red);display:block;line-height:12px}
.news-item p{font-size:9.5px;line-height:14.5px;margin-top:2px;width:405px}
.view-all{width:64px;height:22px;font-size:10px;border-radius:11px}

.testimonials{left:619px;top:568px;width:253px}
.quote{margin-top:9px;border:1px solid #e2e2e2;box-shadow:0 1px 3px rgba(0,0,0,.1);padding:13px 16px;font-size:9.6px;line-height:16px;font-style:italic;color:#777;position:relative;height:92px}
.quote::after{content:"";position:absolute;left:18px;bottom:-8px;width:12px;height:12px;background:#fff;border-right:1px solid #e2e2e2;border-bottom:1px solid #e2e2e2;transform:rotate(45deg) skew(10deg,10deg)}
.dots{display:flex;gap:3px}
.dots i{width:4px;height:4px;border-radius:50%;background:#cfe4f0;display:block}
.dots i.on{background:#3db4e7}
.dots.red i{background:#f1c6c6}
.dots.red i.on{background:var(--red)}
.author{font-size:10px;font-style:italic;color:#3db4e7}
.equipment{left:617px;top:728px;width:255px}
.equip-photo{margin-top:11px;width:254px;height:109px;border:1px solid #e2e2e2;background:linear-gradient(#fff,#eef0f2 55%,#c9cdd1 75%,#fff 100%)}

/* footer */
.footer{left:0;top:946px;width:951px;height:210px;background:var(--footer)}
.cta-bar{left:79px;top:946px;width:793px;height:58px;display:flex;background:var(--red);border-bottom:3px solid var(--red-dark)}
.cta-bar a{flex:1;display:flex;align-items:center;justify-content:center;gap:8px;color:#fff;font-size:18px;font-weight:400;letter-spacing:-.4px;border-right:1px solid #b22a2e}
.cta-bar a:last-child{border-right:none}
.foot-col{top:1020px}
.foot-col h5{font-size:11.5px;font-weight:600;color:#fff;margin-bottom:5px}
.foot-col li{list-style:none;font-size:9.4px;line-height:16px;color:var(--footer-text)}
.social{display:flex;gap:12px;margin-top:8px}
.social span{width:14px;height:14px;border-radius:50%;background:var(--red);display:block}
.newsletter{margin-top:9px;width:194px;height:22px;background:#111;border:1px solid #3a3a3a}
.submit{margin-top:7px;width:43px;height:14px;font-size:7px;border-radius:7px}
.copyright{left:0;top:1172px;width:951px;text-align:center;font-size:10px;color:#555}
</style>
</head>
<body>

<div class="abs utility">
  <ul>
    <li><svg width="7" height="7" viewBox="0 0 10 10"><circle cx="6.5" cy="3.5" r="3" fill="#d33"/><path d="M4 6 1 9" stroke="#d33" stroke-width="2"/></svg>Login</li>
    <li><svg width="9" height="8" viewBox="0 0 12 10"><path d="M1 1h10v6H5l-3 3V7H1z" fill="#d33"/></svg>Blog</li>
    <li><svg width="8" height="8" viewBox="0 0 10 10"><path d="M2 1l2 2-1 1.5c.8 1.4 1.6 2.2 3 3L7.5 6l2 2L8 9.5C4 9 1 6 .5 2z" fill="#d33"/></svg>Contact Us</li>
  </ul>
</div>

<div class="abs brand"><span class="mark"></span>KLMVxco.</div>
<div class="abs call">Call : <strong>555-384-7290</strong></div>
<a class="abs place-order" href="#">
  <svg width="15" height="15" viewBox="0 0 16 16"><rect x="1.5" y="2.5" width="12" height="12" rx="1" fill="none" stroke="#fff" stroke-width="1.6"/><path d="M6 10l1-3 6-6 2 2-6 6z" fill="#fff"/></svg>
  PLACE ORDER
</a>

<ul class="abs main-nav">
  <li class="active" style="width:132px">THE KLMVXCO DIFFERENCE</li>
  <li style="width:44px">ABOUT</li>
  <li style="width:79px">SUSTAINABILITY</li>
  <li style="width:111px">PRODUCTS &amp; SERVICES</li>
  <li style="width:78px">REPROGRAPHICS</li>
  <li style="width:131px">DIGITAL FILE MANAGEMENT</li>
  <li style="width:88px">COLOR GRAPHICS</li>
  <li style="flex:1">EQUIPMENT &amp; SUPPLIES</li>
</ul>
<div class="abs nav-rule"></div>

<div class="abs hero-art" role="img" aria-label="Colour swatch fan, tape measure and pencil resting on rolled architectural plans"></div>
<h1 class="abs hero-title">Services for Architects,<br>Engineers &amp; Builders</h1>
<p class="abs hero-copy">Le Lorem Ipsum est simplement du faux texte employé dans la composition et la mise en page avant impression. Le Lorem Ipsum est le faux texte standard de l'imprimerie depuis les années.</p>
<a class="abs btn-red read-more-hero" href="#">READ MORE</a>

<div class="abs section-rule"></div>
<section class="abs divisions">
  <article class="division">
    <h2><svg width="14" height="14" viewBox="0 0 20 20"><path d="M10 1l2.7 6 6.3.6-4.8 4.3 1.4 6.3L10 15l-5.6 3.2 1.4-6.3L1 7.6 7.3 7z" fill="#fff"/></svg>Reprographics Company</h2>
    <p>On sait depuis longtemps que travailler avec du texte lisible et contenant du sens est source de distractions, et empêche de se.</p>
    <a class="more" href="#">Read More <svg width="11" height="9" viewBox="0 0 12 10"><path d="M1 9c1-4 4-5 7-5V1l4 4-4 4V6C5 6 3 7 1 9z" fill="#fff"/></svg></a>
  </article>
  <article class="division">
    <h2><svg width="14" height="14" viewBox="0 0 20 20"><path d="M10 1l2.7 6 6.3.6-4.8 4.3 1.4 6.3L10 15l-5.6 3.2 1.4-6.3L1 7.6 7.3 7z" fill="#fff"/></svg>Digital Technologies</h2>
    <p>On sait depuis longtemps que travailler avec du texte lisible et contenant du sens est source de distractions, et empêche de se.</p>
    <a class="more" href="#">Read More <svg width="11" height="9" viewBox="0 0 12 10"><path d="M1 9c1-4 4-5 7-5V1l4 4-4 4V6C5 6 3 7 1 9z" fill="#fff"/></svg></a>
  </article>
  <article class="division">
    <h2><svg width="14" height="14" viewBox="0 0 20 20"><path d="M10 1l2.7 6 6.3.6-4.8 4.3 1.4 6.3L10 15l-5.6 3.2 1.4-6.3L1 7.6 7.3 7z" fill="#fff"/></svg>Digital File Management</h2>
    <p>On sait depuis longtemps que travailler avec du texte lisible et contenant du sens est source de distractions, et empêche de se.</p>
    <a class="more" href="#">Read More <svg width="11" height="9" viewBox="0 0 12 10"><path d="M1 9c1-4 4-5 7-5V1l4 4-4 4V6C5 6 3 7 1 9z" fill="#fff"/></svg></a>
  </article>
  <article class="division">
    <h2><svg width="14" height="14" viewBox="0 0 20 20"><path d="M10 1l2.7 6 6.3.6-4.8 4.3 1.4 6.3L10 15l-5.6 3.2 1.4-6.3L1 7.6 7.3 7z" fill="#fff"/></svg>Graphic imaging services</h2>
    <p>On sait depuis longtemps que travailler avec du texte lisible et contenant du sens est source de distractions, et empêche de se.</p>
    <a class="more" href="#">Read More <svg width="11" height="9" viewBox="0 0 12 10"><path d="M1 9c1-4 4-5 7-5V1l4 4-4 4V6C5 6 3 7 1 9z" fill="#fff"/></svg></a>
  </article>
</section>

<section class="abs welcome">
  <h3 class="title">Welcome to KLMVxco.</h3>
  <p>Contrairement à une opinion répandue, le Lorem Ipsum n'est pas simplement du texte aléatoire. Il trouve ses racines dans une oeuvre de la littérature latine classique datant de 45 av. J.-C., le rendant vieux de 2000 ans. Un professeur du Harlowe-Dane College.</p>
  <p>En Virginie, s'est intéressé à un des mots latins les plus obscurs, consectetur, extrait d'un passage du Lorem Ipsum, et en étudiant tous les usages de ce mot dans la littérature classique, découvrit la source incontestable du Lorem Ipsum. Il provient en fait des sections.</p>
</section>

<section class="abs news">
  <h4 class="title">Recent News</h4>
  <div class="news-item">
    <div class="thumb" role="img" aria-label="Rolled blueprints"></div>
    <div><time>21st March, 2013</time><p>Contrairement à une opinion répandue, le Lorem Ipsum n'est pas simplement du texte aléatoire. Il trouve ses racines dans une oeuvre de la littérature latine classique datant de 45 av. J.-C., le rendant vieux de 2000 ans.</p></div>
  </div>
  <div class="news-item">
    <div class="thumb" role="img" aria-label="Blue technical blueprint drawing"></div>
    <div><time>22nd March, 2013</time><p>Contrairement à une opinion répandue, le Lorem Ipsum n'est pas simplement du texte aléatoire. Il trouve ses racines dans une oeuvre de la littérature latine classique datant de 45 av. J.-C., le rendant vieux de 2000 ans.</p></div>
  </div>
</section>
<a class="abs btn-red view-all" href="#" style="left:80px;top:897px">VIEW ALL</a>

<section class="abs testimonials">
  <h3 class="title">Testimonials</h3>
  <blockquote class="quote">Plusieurs variations de Lorem Ipsum peuvent être trouvées ici ou là, mais la majeure partie d'entre elles a été altérée par l'addition d'humour ou de mots aléatoires qui.</blockquote>
</section>
<div class="abs dots" style="left:653px;top:708px"><i class="on"></i><i></i><i></i></div>
<div class="abs author" style="left:801px;top:703px">Orwen Baleth</div>

<section class="abs equipment">
  <h4 class="title">Equipment for Sale</h4>
  <div class="equip-photo" role="img" aria-label="Large format printers and scanner system for sale"></div>
</section>
<div class="abs dots red" style="left:622px;top:877px"><i class="on"></i><i></i><i></i></div>
<a class="abs btn-red view-all" href="#" style="left:620px;top:897px;width:63px">VIEW ALL</a>

<footer>
  <div class="abs footer"></div>
  <nav class="abs cta-bar">
    <a href="#"><svg width="17" height="19" viewBox="0 0 17 19"><rect x="1" y="3" width="15" height="15" rx="1" fill="none" stroke="#fff" stroke-width="1.6"/><path d="M5 1v4M12 1v4M8.5 14V8M6 10.5l2.5-2.5 2.5 2.5" stroke="#fff" stroke-width="1.6" fill="none"/></svg>Order Form &amp; Upload File</a>
    <a href="#"><svg width="20" height="20" viewBox="0 0 20 20"><circle cx="10" cy="10" r="7" fill="none" stroke="#fff" stroke-width="1.8"/><circle cx="10" cy="10" r="2.6" fill="#fff"/><circle cx="10" cy="3" r="2.2" fill="#fff"/><circle cx="3.5" cy="13.5" r="2.2" fill="#fff"/><circle cx="16.5" cy="13.5" r="2.2" fill="#fff"/></svg>Digital Plan-room</a>
    <a href="#"><svg width="17" height="19" viewBox="0 0 17 19"><rect x="1" y="3" width="15" height="15" rx="1" fill="none" stroke="#fff" stroke-width="1.6"/><path d="M4 1v4M8.5 1v4M13 1v4M4 8h9M4 11h9M4 14h9" stroke="#fff" stroke-width="1.4"/></svg>Get a Free Quote</a>
  </nav>

  <div class="abs foot-col" style="left:79px"><h5>About Us</h5><ul><li>Plusieurs</li><li>Variations de</li><li>Lorem Ipsum</li><li>Peuventêtre</li><li>Trouvées ici</li><li>Mais la majeure</li></ul></div>
  <div class="abs foot-col" style="left:223px"><h5>Products &amp; Services</h5><ul><li>Plusieurs</li><li>Variations de</li><li>Lorem Ipsum</li><li>Peuventêtre</li></ul></div>
  <div class="abs foot-col" style="left:394px"><h5>Color Graphics</h5><ul><li>Plusieurs</li><li>Variations de</li><li>Lorem Ipsum</li></ul></div>
  <div class="abs foot-col" style="left:545px"><h5>Blog</h5><ul><li>Plusieurs</li><li>Variations de</li><li>Lorem Ipsum</li><li>Peuventêtre</li><li>Trouvées ici</li></ul></div>
  <div class="abs foot-col" style="left:678px">
    <h5>Follow Us on</h5>
    <div class="social"><span aria-label="QN"></span><span aria-label="Chirpa"></span><span aria-label="Workrung"></span></div>
    <h5 style="margin-top:12px">Newsletter Sign Up</h5>
    <div class="newsletter"></div>
    <div class="btn-red submit">SUBMIT</div>
  </div>
</footer>

<p class="abs copyright">Copyright 2013 KLMVxco. Northvale Office (555) 384-7290 Questions/Comments: email us at info@klmvxco.example</p>

</body>
</html>
```